Valdane Companies Business Card Design

We need a new business card for our Private Equity Real Estate Development firm, “Valdane” and our EB-5 regional center “Thornmere Regional Center” on one card. We prefer a design that is simple, elegant, and represents the luxury products we design and build as well as the financial security and stability our successful history has produced. We are an industry leader in our field and 3rd generation family business that has evolved into an institutional quality investment platform. Considered design size is standard business card dimensions (3.5 x 2 inches with an additional 1/8 inch space for design elements or backgrounds that extend beyond the finished size of your piece.

Target Market(s)

• High net worth individuals
• Highly skilled technical workers and physicians in the US seeking investment-based immigration opportunities
• Sophisticated private equity investors
• Intermediary partners include domestic attorneys and investment brokers, as well as international agent networks
• US real estate developers

Industry/Entity Type

Finance

Contact Information for Business Card

(Providing placeholder info for personal information, please design for longer character spaces, longer names and addresses etc..)
• Logo for Valdane
• Logo for Thornmere Regional Center
• Full name: Marcus Valdane
• Job title: CEO
• Email address: mvaldane@valdanecompanies.com
• Cell phone number: +1.555.314.2287
• Office number +1.555.628.4410
• Office address: Larkfield Court 5, 4817 Vista Orilla, Corvell Heights, CV.
• Website: www.valdanecompanies.com

Font styles to use
Serif
Sans Serif

Colors
ec1f27
ffffff
000000

Requirements
Must have
• • Logo for Valdane
• • Logo for Thornmere Regional Center
• - Use rounded corners
• (See .ai file included for logos)
Nice to have
• • Simple, elegant design
• • Aesthetically compatible with our website design (www.valdanecompanies.com)
• • Color palette including but not limited to white, black, and red (as per logos)
Should not have
• - Not too much red color
• - Do not stack both logos on top of each other

```html
<!DOCTYPE html>
<html lang="en">
<head>
<meta charset="utf-8">
<title>Valdane Companies – Business Card</title>
<link href="https://fonts.googleapis.com/css2?family=Lato:wght@400;700&family=Oswald:wght@500&display=swap" rel="stylesheet">
<style>
  :root {
    --red: #ec1f27;
    --logo-red: #c21a2c;
    --white: #ffffff;
    --black: #000000;
    --stage: #1b1b1b;
    --card-dark: #141414;
    --card-light: #2b2b2b;
  }
  * { margin: 0; padding: 0; box-sizing: border-box; }
  html, body {
    width: 1200px; height: 900px; overflow: hidden;
    background: var(--stage);
    font-family: "Lato", sans-serif;
  }
  .canvas {
    position: relative; width: 1200px; height: 900px;
    background: var(--stage);
  }
  .card {
    position: absolute; left: 250px; width: 700px; height: 400px;
    border-radius: 18px;
    background: linear-gradient(135deg, var(--card-dark) 0%, #1c1c1c 55%, var(--card-light) 100%);
    box-shadow: 0 10px 30px rgba(0,0,0,0.55);
    overflow: hidden;
  }
  .card--front { top: 35px; }
  .card--back { top: 465px; }

  /* Front: regional center wordmark */
  .wordmark {
    position: absolute; left: 0; right: 0; top: 0; bottom: 0;
    display: flex; align-items: center; justify-content: center; gap: 18px;
  }
  .wordmark__square {
    width: 30px; height: 30px; background: var(--logo-red);
  }
  .wordmark__name {
    font-family: "Lato", sans-serif; font-weight: 400;
    color: var(--logo-red);
    font-size: 30px; letter-spacing: 5px; text-transform: uppercase;
  }

  /* Back: contact side */
  .identity {
    position: absolute; right: 355px; top: 118px; text-align: right;
  }
  .identity__name {
    font-family: "Oswald", sans-serif; font-weight: 500;
    font-size: 42px; line-height: 1; color: var(--red);
    text-transform: uppercase; letter-spacing: 0.5px;
    white-space: nowrap;
  }
  .identity__title {
    margin-top: 8px; font-size: 16px; color: var(--white); letter-spacing: 1px;
  }
  .divider {
    position: absolute; left: 362px; top: 108px; width: 2px; height: 86px;
    background: var(--red);
  }
  .contacts {
    position: absolute; left: 382px; top: 106px; list-style: none;
  }
  .contacts__item {
    display: flex; align-items: center; gap: 10px;
    font-size: 16px; line-height: 22px; color: var(--white);
    white-space: nowrap;
  }
  .contacts__icon { width: 11px; height: 11px; flex: none; }
  .contacts__accent { color: var(--red); }
  .address {
    position: absolute; left: 0; right: 0; top: 300px;
    text-align: center; font-size: 18px; color: var(--white);
  }
</style>
</head>
<body>
<main class="canvas">

  <section class="card card--front" aria-label="Card front">
    <div class="wordmark">
      <span class="wordmark__square"></span>
      <span class="wordmark__name">Thornmere Regional Center</span>
    </div>
  </section>

  <section class="card card--back" aria-label="Card back">
    <div class="identity">
      <h1 class="identity__name">Marcus Valdane</h1>
      <p class="identity__title">CEO</p>
    </div>
    <span class="divider"></span>
    <ul class="contacts">
      <li class="contacts__item">
        <svg class="contacts__icon" viewBox="0 0 12 12"><path d="M2.5 1l2 2.5-1.2 1.3c.6 1.5 1.8 2.7 3.3 3.3L7.9 7l2.6 2-1 2C5 11 1 7 1 2.4z" fill="var(--red)"/></svg>
        +1.555.314.2287
      </li>
      <li class="contacts__item">
        <svg class="contacts__icon" viewBox="0 0 12 12"><rect x="3" y="1" width="6" height="3" fill="var(--red)"/><rect x="1" y="4.5" width="10" height="4.5" rx="1" fill="var(--red)"/><rect x="3" y="8" width="6" height="3" fill="var(--red)"/></svg>
        +1.555.628.4410
      </li>
      <li class="contacts__item">
        <svg class="contacts__icon" viewBox="0 0 12 12"><rect x="1" y="2.5" width="10" height="7" fill="none" stroke="var(--red)" stroke-width="1.2"/><path d="M1 2.5l5 4 5-4" fill="none" stroke="var(--red)" stroke-width="1.2"/></svg>
        mvaldane@valdanecompanies.com
      </li>
      <li class="contacts__item">
        <svg class="contacts__icon" viewBox="0 0 12 12"><circle cx="6" cy="6" r="5" fill="none" stroke="var(--red)" stroke-width="1.1"/><ellipse cx="6" cy="6" rx="2.2" ry="5" fill="none" stroke="var(--red)" stroke-width="1"/><path d="M1 6h10" stroke="var(--red)" stroke-width="1"/></svg>
        <span>www.<span class="contacts__accent">valdanecompanies</span>.com</span>
      </li>
    </ul>
    <p class="address">Larkfield Court 5, 4817 Vista Orilla, Corvell Heights, CV.</p>
  </section>

</main>
</body>
</html>
```